Software allocation system needs a business card design

We need a business card designed for our software platform - www.tallivo.com.au

At the moment the logo and website is all black and white, we are happy for suggestions on implementing some colour throughout either the logo or business card.

Industry/Entity Type

Software

Font styles to use
Sans Serif

Colors

Designer to choose colors to be used in the design.

```html
<!DOCTYPE html>
<html lang="en">
<head>
<meta charset="utf-8">
<title>Tallivo Business Card</title>
<link rel="stylesheet" href="https://fonts.googleapis.com/css2?family=Questrial&display=swap">
<style>
  :root {
    --page-bg: #e9e9e7;
    --card-dark: #1c1d1d;
    --brand-blue: #2b9ad6;
    --tagline-teal: #a4d6de;
    --contact-grey: #b9d3d8;
    --arc-line: #cfeef0;
    --mark-white: #ffffff;
  }
  * { margin: 0; padding: 0; box-sizing: border-box; }
  html, body {
    width: 1200px;
    height: 900px;
    overflow: hidden;
    background: var(--page-bg);
    font-family: "Questrial", sans-serif;
  }
  .business-card {
    position: absolute;
    left: 75px;
    top: 150px;
    width: 1050px;
    height: 600px;
    background: var(--card-dark);
    overflow: hidden;
    box-shadow: 0 12px 30px rgba(0,0,0,0.18);
  }
  .corner-graphic {
    position: absolute;
    inset: 0;
    width: 1050px;
    height: 600px;
  }
  .brand-block {
    position: absolute;
    left: 120px;
    top: 170px;
  }
  .brand-name {
    display: flex;
    align-items: center;
    gap: 16px;
    color: var(--brand-blue);
    font-size: 74px;
    letter-spacing: 6px;
    line-height: 1;
  }
  .brand-dot {
    width: 30px;
    height: 30px;
    border-radius: 50%;
    background: var(--mark-white);
    flex: none;
  }
  .brand-tagline {
    margin-top: 26px;
    color: var(--tagline-teal);
    font-size: 21px;
    letter-spacing: 2.4px;
    text-transform: uppercase;
  }
  .contact-block {
    position: absolute;
    left: 330px;
    top: 390px;
  }
  .contact-heading {
    color: var(--brand-blue);
    font-size: 32px;
    margin-bottom: 12px;
  }
  .contact-line {
    color: var(--contact-grey);
    font-size: 25px;
    line-height: 1.45;
  }
</style>
</head>
<body>
  <div class="business-card">
    <svg class="corner-graphic" viewBox="0 0 1050 600" aria-hidden="true">
      <g fill="none" stroke="var(--arc-line)" stroke-width="3">
        <circle cx="1050" cy="120" r="318"/>
        <circle cx="1050" cy="120" r="330"/>
        <circle cx="1050" cy="120" r="342"/>
        <circle cx="1050" cy="120" r="354"/>
        <circle cx="1050" cy="120" r="366"/>
      </g>
      <circle cx="1050" cy="120" r="305" fill="var(--brand-blue)"/>
    </svg>

    <div class="brand-block">
      <div class="brand-name"><span class="brand-dot"></span>TALLIVO</div>
      <p class="brand-tagline">Planning &amp; Compliance for Heavy Industry</p>
    </div>

    <div class="contact-block">
      <h2 class="contact-heading">Contac Us</h2>
      <p class="contact-line">PO Box 318</p>
      <p class="contact-line">Hollow Bay NSW 2270</p>
      <p class="contact-line">hello@tallivo.com.au</p>
    </div>
  </div>
</body>
</html>
```